Meadow Gate Labradoodle web design

We're a new labradoodle breeder in Charleston, SC in need of a web design.

Our name is Meadow Gate Labradoodles.

Site we like: http://www.pebblefieldlabradoodles.com/
http://www.quillbrookfarmlabradoodles.com/

Logo Font:
The ''Meadow Gate'' font is called TestarossaNF and is available freely at http://www.glyphtrove.com/velmorina-nf.font.  The ''Labradoodles'' font is called Worstveld Sling Extra and is available freely at http://www.typebasketzone.com/KorvandelHookExtra.php.

Requirements
Must have
• Our logo
1. Home page
2. Labradoodle F.A.Q.
3. Our doodles
4. Availability
5. Adoption Process
6. Contact us
Link/badge icon for Health Guarantee
Nice to have
• Color and font to match the logo.

An area to add pictures
Should not have
• Rainbows
Rainbow colors

```html
<!DOCTYPE html>
<html lang="en">
<head>
<meta charset="utf-8">
<title>Meadow Gate Labradoodles</title>
<link rel="stylesheet" href="https://fonts.googleapis.com/css2?family=Federo&family=PT+Sans:ital,wght@0,400;0,700;1,400;1,700&display=swap">
<style>
  :root {
    --pink: #ec7f97;
    --pink-deep: #e4507a;
    --pink-band: #ea8ba1;
    --hero-bg: #efd6d3;
    --beige: #e8dccd;
    --cream: #ecdfd0;
    --heading-brown: #7b6b5c;
    --text-grey: #8f8a86;
    --footer-text: #6e6258;
    --badge-text: #4a4540;
    --white: #ffffff;
    --scroll: #8a8a8a;
  }
  * { box-sizing: border-box; margin: 0; padding: 0; }
  html, body { width: 876px; height: 1200px; overflow: hidden; }
  body {
    position: relative;
    background: var(--white);
    font-family: "PT Sans", Arial, sans-serif;
    color: var(--text-grey);
  }
  .abs { position: absolute; }

  /* Header */
  .site-header { left: 0; top: 0; width: 876px; height: 55px; background: var(--pink); border-bottom: 1px solid #d96d86; }
  .main-nav { right: 60px; top: 18px; display: flex; gap: 22px; }
  .main-nav a {
    font-family: "Federo", Georgia, serif;
    font-variant: small-caps;
    font-size: 19px;
    color: var(--white);
    text-decoration: none;
    text-shadow: 1px 1px 1px rgba(90, 30, 45, .55);
    letter-spacing: .3px;
  }

  /* Hero */
  .hero-band { left: 0; top: 56px; width: 876px; height: 374px; background: linear-gradient(180deg, #f1e1dc, var(--hero-bg)); }
  .hero-photo {
    left: 64px; top: 79px; width: 748px; height: 328px;
    background: radial-gradient(ellipse at 55% 45%, #a24e26 0%, #7a3a1d 55%, #3f2215 100%);
    box-shadow: 0 8px 10px rgba(0,0,0,.35);
  }
  .slider-dots { left: 733px; top: 90px; display: flex; gap: 8px; }
  .slider-dots span { width: 8px; height: 8px; border-radius: 50%; background: rgba(255,255,255,.45); }
  .slider-dots span.active { background: var(--white); }

  .brand-mark { left: 18px; top: 10px; width: 264px; height: 246px; }
  .brand-mark .disc { left: 10px; top: 0; width: 244px; height: 244px; border-radius: 50%; background: var(--pink); }
  .brand-mark .name {
    left: 0; top: 92px; width: 264px; text-align: center;
    font-family: "PT Sans", Arial, sans-serif; font-weight: 700; font-size: 24px; line-height: 30px;
    color: var(--white);
  }

  /* Reserve strip */
  .rule-pink { left: 0; width: 876px; height: 2px; background: var(--pink-deep); }
  .reserve-band { left: 0; top: 438px; width: 876px; height: 62px; background: var(--cream); }
  .reserve-title {
    left: 0; top: 448px; width: 876px; text-align: center;
    font-family: "Federo", Georgia, serif; font-variant: small-caps; font-weight: 400;
    font-size: 36px; color: var(--heading-brown);
    text-shadow: 1px 1px 0 rgba(255,255,255,.6);
  }

  /* Feature */
  .feature-photo {
    left: 64px; top: 532px; width: 363px; height: 238px;
    background: linear-gradient(160deg, #c7a06f 0%, #6f5a3e 40%, #1e1a18 70%, #b59b83 100%);
    box-shadow: 0 10px 10px rgba(0,0,0,.3);
  }
  .story-title {
    font-family: "Federo", Georgia, serif; font-variant: small-caps; font-weight: 400;
    font-size: 16px; color: var(--pink-deep); letter-spacing: .2px; white-space: nowrap;
  }
  .story-text { font-size: 11px; line-height: 13.5px; color: var(--text-grey); }
  .read-more { font-size: 11px; font-style: italic; color: var(--pink-deep); text-decoration: none; white-space: nowrap; }

  .thumb { left: 446px; width: 111px; height: 111px; }
  .thumb-1 { top: 532px; background: linear-gradient(150deg, #5f5a52, #8d8274 50%, #2d2722); }
  .thumb-2 { top: 659px; background: linear-gradient(150deg, #6a5b4e, #e6e1da 55%, #8d8376); }
  .thumb-3 { top: 787px; background: radial-gradient(circle at 50% 55%, #3a2618, #6b3d2a 45%, #c9a48f 100%); }

  .scroll-track { left: 832px; top: 550px; width: 6px; height: 336px; border-radius: 3px; background: var(--scroll); }
  .scroll-thumb { left: 831px; top: 680px; width: 8px; height: 60px; border-radius: 4px; background: #f2f2f2; border: 1px solid #9a9a9a; }

  /* Footer */
  .footer-band { left: 0; top: 928px; width: 876px; height: 38px; background: var(--pink-band); border-top: 1px solid var(--pink-deep); }
  .site-footer { left: 0; top: 966px; width: 876px; height: 234px; background: var(--beige); }
  .footer-mark { left: 75px; top: 890px; width: 118px; height: 114px; }
  .footer-mark .disc { left: 2px; top: 0; width: 114px; height: 114px; border-radius: 50%; background: var(--pink); }
  .footer-mark .name {
    left: 0; top: 40px; width: 118px; text-align: center;
    font-weight: 700; font-size: 13px; line-height: 16px; color: var(--white);
  }
  .footer-heading {
    font-family: "Federo", Georgia, serif; font-variant: small-caps; font-weight: 400;
    font-size: 13px; color: #3f3731; letter-spacing: .3px;
  }
  .footer-text { font-size: 11px; line-height: 13.5px; color: var(--footer-text); }
  .footer-text .handle, .footer-text .link { color: var(--pink-deep); }
  .footer-text .link { font-style: italic; }
  .tweet-time { font-size: 9px; color: var(--footer-text); }
  .footer-link { font-size: 11px; font-weight: 700; color: var(--pink-deep); text-decoration: none; }
  .footer-link.italic { font-style: italic; }
  .post-title { font-size: 10px; font-weight: 700; color: var(--footer-text); white-space: nowrap; }
  .post-meta { font-size: 11px; font-style: italic; color: var(--footer-text); }

  /* Health guarantee badge */
  .health-badge { left: 693px; top: 1000px; width: 120px; height: 168px; }
  .badge-label {
    left: 693px; top: 1029px; width: 120px; text-align: center;
    font-family: "PT Sans", Arial, sans-serif; color: var(--badge-text);
  }
  .badge-label .percent { display: block; font-size: 17px; line-height: 18px; color: var(--pink-deep); }
  .badge-label .word-health { display: block; font-size: 23px; line-height: 23px; }
  .badge-label .word-guarantee { display: block; font-size: 17px; line-height: 19px; }
</style>
</head>
<body>

<header class="site-header abs">
  <nav class="main-nav abs">
    <a href="#">Home</a>
    <a href="#">Availability</a>
    <a href="#">Process</a>
    <a href="#">Our Doodles</a>
    <a href="#">Contact</a>
    <a href="#">F.A.Q.</a>
  </nav>
</header>

<div class="hero-band abs"></div>
<div class="hero-photo abs" role="img" aria-label="Photo of a red labradoodle lying on a wooden floor"></div>
<div class="slider-dots abs"><span class="active"></span><span></span><span></span><span></span></div>

<div class="brand-mark abs">
  <div class="disc abs"></div>
  <div class="name abs">Meadow Gate<br>Labradoodles</div>
</div>

<div class="rule-pink abs" style="top:436px"></div>
<div class="reserve-band abs"></div>
<h1 class="reserve-title abs">Reserve Yours Today!</h1>
<div class="rule-pink abs" style="top:500px"></div>

<main>
  <article>
    <div class="feature-photo abs" role="img" aria-label="Photo of a black labradoodle puppy playing with a yellow ball"></div>
    <h2 class="story-title abs" style="left:64px; top:795px;">Even Marla Winslow has one!</h2>
    <p class="story-text abs" style="left:64px; top:826px; width:360px;">Proin gravida nibh vel velit auctor aliquet. Aenean sollicitudin, lorem quis bibendum auctor, nisi elit consequat ipsum, nec sagittis sem nibh id elit. Proin gravida nibh vel velit auctor aliquet. Aenean sollicitudin, lorem quis bibendum auctor.</p>
    <a class="read-more abs" href="#" style="left:340px; top:881px;">Continue reading...</a>
  </article>

  <section class="success-stories">
    <div class="thumb thumb-1 abs" role="img" aria-label="Photo of Lucky, a parti-coloured labradoodle"></div>
    <h2 class="story-title abs" style="left:574px; top:529px;">Lucky's Success Story</h2>
    <p class="story-text abs" style="left:574px; top:563px; width:242px;">Proin gravida nibh vel velit auctor aliquet. Aenean sollicitudin, lorem quis bibendum auctor, nisi elit consequat ipsum, nec sagittis sem nibh id elit.</p>
    <a class="read-more abs" href="#" style="left:722px; top:618px;">Continue reading...</a>

    <div class="thumb thumb-2 abs" role="img" aria-label="Photo of Purvis, a white labradoodle"></div>
    <h2 class="story-title abs" style="left:574px; top:656px;">Purvis's Success Story</h2>
    <p class="story-text abs" style="left:574px; top:690px; width:242px;">Proin gravida nibh vel velit auctor aliquet. Aenean sollicitudin, lorem quis bibendum auctor, nisi elit consequat ipsum, nec sagittis sem nibh id elit.</p>
    <a class="read-more abs" href="#" style="left:722px; top:745px;">Continue reading...</a>

    <div class="thumb thumb-3 abs" role="img" aria-label="Photo of Charlie, a newborn chocolate puppy held in a hand"></div>
    <h2 class="story-title abs" style="left:574px; top:784px;">Charlie's Success Story</h2>
    <p class="story-text abs" style="left:574px; top:826px; width:242px;">Proin gravida nibh vel velit auctor aliquet. Aenean sollicitudin, lorem quis bibendum auctor, nisi elit consequat ipsum, nec sagittis sem nibh id elit.</p>
    <a class="read-more abs" href="#" style="left:722px; top:881px;">Continue reading...</a>

    <div class="scroll-track abs"></div>
    <div class="scroll-thumb abs"></div>
  </section>
</main>

<div class="footer-band abs"></div>
<footer class="site-footer abs"></footer>

<div class="footer-mark abs">
  <div class="disc abs"></div>
  <div class="name abs">Meadow Gate<br>Labradoodles</div>
</div>

<div class="footer-text abs" style="left:64px; top:1021px; width:172px;">
  <p>Your about us information would fit here nicely.</p>
  <p style="margin-top:13px;">You could also just have an overview and use the link below to link to your full about us page.</p>
</div>
<a class="footer-link abs" href="#" style="left:64px; top:1117px;">Find out more...</a>

<h3 class="footer-heading abs" style="left:256px; top:988px;">Chatter Feed</h3>
<div class="footer-text abs" style="left:256px; top:1015px; width:175px;">
  <p>hey <span class="handle">@junebrightwell</span> just got my design proofs back from Fern Cottage Design, so excited!</p>
  <p class="tweet-time" style="margin-top:7px;">1 day ago</p>
  <p style="margin-top:10px;">Just purchased <span class="handle">@ferncottage</span>'s awesome new ebook on owning a website, good read.</p>
  <p class="link">www.ferncottagedesign.com</p>
</div>

<h3 class="footer-heading abs" style="left:447px; top:988px;">Latest Post</h3>
<p class="post-title abs" style="left:447px; top:1015px;">Your article title copy should fit here nicely!</p>
<p class="post-meta abs" style="left:447px; top:1040px;">May 22, 2011 &bull; 1 Comment</p>
<p class="footer-text abs" style="left:447px; top:1067px; width:180px;">This would be a great place to have a descriptive excerpt from your most recent blog or news article.</p>
<a class="footer-link italic abs" href="#" style="left:447px; top:1129px;">Continue reading...</a>

<svg class="health-badge abs" viewBox="0 0 120 168" aria-hidden="true">
  <defs>
    <linearGradient id="badge-silver" x1="0" y1="0" x2="0" y2="1">
      <stop offset="0" stop-color="#ffffff"/>
      <stop offset="0.5" stop-color="#d4d4d4"/>
      <stop offset="1" stop-color="#9c9c9c"/>
    </linearGradient>
  </defs>
  <polygon points="28,100 50,110 38,166 28,150 14,160" fill="#7a746f"/>
  <polygon points="92,100 70,110 82,166 92,150 106,160" fill="#7a746f"/>
  <circle cx="60" cy="60" r="55" fill="url(#badge-silver)" stroke="url(#badge-silver)" stroke-width="7" stroke-dasharray="4 4"/>
</svg>
<a class="badge-label abs" href="#" style="text-decoration:none;">
  <span class="percent">100%</span>
  <span class="word-health">Health</span>
  <span class="word-guarantee">Guarantee</span>
</a>

</body>
</html>
```